Construction material supplies company business card ****

1. Full company name “K T Masonry Works Ltd”
I am after a Business card design for the company as a whole. We are better known in Solomon Islands as “K T Masonry” for short.

We are a building materials supplier of
Ready Mixed Concrete, Bricks and Blocks,
Quarry products- gravel, aggregates, sand etc.
Cement distributor/retailer of reputable brands.
Other prefab concrete products. Culverts, wave breakers, concrete retaining blocks etc.

2. Competitive Advantage over Competition: Quality, efficient, professional, dependable, reliable

3. We want people to feel trust worthy, high quality, strong when they see our brand

5. No preference to color. Maybe more sturdy and corporate. Not fancy.

Industry/Entity Type

CONSTRUCTION SUPPLY

Contact Information for Business Card

Name, Position, office phone mob phone, email

Requirements
Must have
• the company logo
Nice to have
• would like to see a mixture of designs, of with logo only and also with simple graphic designs to bring out the company whilst still have the strong sturdy professional feeling

```html
<!DOCTYPE html>
<html lang="en">
<head>
<meta charset="utf-8">
<title>K T Masonry – Business Card</title>
<link href="https://fonts.googleapis.com/css2?family=Roboto:wght@400;700&display=swap" rel="stylesheet">
<style>
  :root {
    --backdrop: #94969b;
    --navy: #11446a;
    --paper: #f0eef3;
    --ink-soft: #4f5259;
    --white: #ffffff;
  }
  * { box-sizing: border-box; margin: 0; padding: 0; }
  html, body {
    width: 1200px;
    height: 900px;
    overflow: hidden;
    background: var(--backdrop);
    font-family: "Roboto", Arial, sans-serif;
  }
  .card {
    position: absolute;
    left: 363px;
    width: 475px;
    height: 271px;
  }
  .card--front {
    top: 145px;
    background: var(--navy);
    display: flex;
    align-items: center;
    justify-content: center;
  }
  .card--back {
    top: 484px;
    background: var(--paper);
  }
  .wordmark {
    font-weight: 700;
    letter-spacing: 0.04em;
    text-transform: uppercase;
    white-space: nowrap;
    line-height: 1;
  }
  .card--front .wordmark {
    color: var(--white);
    font-size: 34px;
  }
  .card--back .wordmark {
    position: absolute;
    left: 42px;
    top: 124px;
    color: var(--navy);
    font-size: 22px;
  }
  .divider {
    position: absolute;
    left: 237px;
    top: 78px;
    width: 1px;
    height: 114px;
    background: var(--navy);
  }
  .details {
    position: absolute;
    left: 254px;
    top: 76px;
  }
  .person-name {
    color: var(--navy);
    font-weight: 700;
    font-size: 15px;
    text-transform: uppercase;
    line-height: 18px;
  }
  .person-role {
    color: var(--ink-soft);
    font-size: 11px;
    margin-top: 1px;
  }
  .contact-list {
    list-style: none;
    margin-top: 30px;
  }
  .contact-list li {
    display: flex;
    align-items: center;
    gap: 7px;
    color: var(--ink-soft);
    font-size: 11px;
    height: 15.4px;
  }
  .contact-list svg {
    width: 8px;
    height: 8px;
    fill: var(--ink-soft);
    flex: none;
  }
</style>
</head>
<body>
  <section class="card card--front">
    <span class="wordmark">K T Masonry</span>
  </section>

  <section class="card card--back">
    <span class="wordmark">K T Masonry</span>
    <div class="divider"></div>
    <div class="details">
      <p class="person-name">Marcus Telford</p>
      <p class="person-role">Director</p>
      <ul class="contact-list">
        <li>
          <svg viewBox="0 0 10 10"><path d="M2.5 0h5a1 1 0 0 1 1 1v8a1 1 0 0 1-1 1h-5a1 1 0 0 1-1-1V1a1 1 0 0 1 1-1zm.3 1.4v6.2h4.4V1.4z"/></svg>
          720.555.0148
        </li>
        <li>
          <svg viewBox="0 0 10 10"><path d="M2 0.5l1.6 2.2-.9 1a6 6 0 0 0 2.9 2.9l1-.9L8.8 7.3 8 9.2C4 9 1 6 .8 2z"/></svg>
          855.555.0172
        </li>
        <li>
          <svg viewBox="0 0 10 10"><path d="M0 2h10v6H0zm1 1l4 2.8L9 3z" fill-rule="evenodd"/></svg>
          mtelford@ktmasonry.com
        </li>
        <li>
          <svg viewBox="0 0 10 10"><circle cx="5" cy="5" r="4.5"/><path d="M0.5 5h9M5 .5v9" stroke="#f0eef3" stroke-width="0.8"/></svg>
          www.ktmasonry.com
        </li>
      </ul>
    </div>
  </section>
</body>
</html>
```